Bayward Vale Physiotherapy Website www.baywardvalephysiotherapy.com.au

Create Wordpress website for Bayward Vale Physiotherapy which aligns with our other locations www.oakmerephysiotherapy,com.au. We would like the website to present in a similar fashion to our exisiting site with similar headings and layout. We will then alter the text to make it location specific.

Coding

Coded - Design and coding required

Number of Pages Required

1 page

Font styles to use
Sans Serif

Requirements
Must have
• Colours of the website must match the colours of the colour Bayward Vale Physiotherapy logo
• Website must be complimentary to existing websites,
• www.oakmerephysiotherapy.com.au
• www.oakmerepilatesandrehab.com.au

```html
<!DOCTYPE html>
<html lang="en">
<head>
<meta charset="utf-8">
<title>Bayward Vale Physiotherapy</title>
<link href="https://fonts.googleapis.com/css2?family=Montserrat:wght@400;600;700&family=Open+Sans:wght@400;600&display=swap" rel="stylesheet">
<style>
:root{
  --navy:#232a5c;
  --teal:#78bea3;
  --teal-dark:#62ad91;
  --text:#4f4f55;
  --light:#f1f1f1;
  --footer:#333333;
  --white:#ffffff;
}
*{box-sizing:border-box;margin:0;padding:0}
html,body{width:1200px;height:2961px;overflow:hidden;background:var(--white)}
body{position:relative;font-family:"Open Sans",Arial,sans-serif;color:var(--text)}
.abs{position:absolute}

/* header + hero */
.hero{left:0;top:0;width:1200px;height:650px;background:linear-gradient(100deg,#e9e9ea 0%,#d8d6d4 45%,#c9b8a8 70%,#b9b2ad 100%)}
.hero-curve{left:0;top:560px;width:1200px;height:100px}
.brand{left:132px;top:26px;font-family:"Montserrat",Arial,sans-serif;font-weight:700;font-size:22px;color:var(--navy);display:flex;align-items:center;gap:10px}
.brand-dot{width:18px;height:18px;border-radius:50%;background:var(--navy)}
.nav{right:118px;top:22px;display:flex;gap:6px;align-items:center;font-size:13px}
.nav a{color:var(--navy);text-decoration:none;padding:4px 8px}
.nav a.active{background:var(--navy);color:var(--white);font-weight:600}
.hero-title{left:132px;top:290px;font-family:"Montserrat",Arial,sans-serif;font-weight:700;font-size:38px;color:var(--navy);letter-spacing:.5px}
.btn{display:inline-block;background:var(--teal-dark);color:var(--white);font-family:"Montserrat",Arial,sans-serif;font-weight:600;font-size:13px;letter-spacing:.5px;text-align:center;box-shadow:0 2px 4px rgba(0,0,0,.2)}
.hero-btn{left:132px;top:360px;width:130px;height:40px;line-height:40px}
.dots{left:590px;top:600px;display:flex;gap:14px}
.dots span{width:8px;height:8px;border-radius:50%;background:var(--white)}
.dots span.on{width:12px;height:12px;margin-top:-2px;border:2px solid var(--white);background:transparent}

/* welcome */
.welcome-title{left:132px;top:712px;font-family:"Montserrat",Arial,sans-serif;font-weight:400;font-size:20px;color:var(--navy);line-height:28px}
.welcome-title b{font-weight:700}
.welcome-copy{left:132px;top:784px;width:530px;font-size:12.5px;line-height:18px}
.welcome-copy p{margin-bottom:14px}
.book-btn{left:136px;top:1050px;width:194px;height:40px;line-height:40px}
.note{left:132px;top:1110px;width:500px;font-size:12px;line-height:18px}
.welcome-photo{left:707px;top:720px;width:362px;height:432px;background:linear-gradient(160deg,#b9a79c 0%,#8f97b5 45%,#d5d8dc 100%);border-left:5px solid var(--navy)}

/* services */
.services{left:0;top:1234px;width:1200px;height:700px}
.section-title{width:1200px;left:0;text-align:center;font-family:"Montserrat",Arial,sans-serif;font-weight:700;font-size:20px;letter-spacing:.5px}
.section-rule{left:568px;width:64px;height:3px;background:var(--teal)}
.services-title{top:1280px;color:var(--white)}
.services-rule{top:1322px}
.grid-line{background:rgba(255,255,255,.12)}
.service{width:300px;text-align:center;color:var(--white)}
.service svg{display:block;margin:0 auto 14px}
.service h3{font-family:"Montserrat",Arial,sans-serif;font-weight:700;font-size:13px;letter-spacing:.3px;margin-bottom:12px}
.service p{font-size:11.5px;line-height:17px;color:#d7d9e6;padding:0 18px}

/* blog */
.blog{left:0;top:1905px;width:1200px;height:540px;background:var(--light)}
.blog-title{top:1978px;color:var(--navy)}
.blog-rule{top:2018px}
.card{top:2067px;width:296px;height:322px;background:var(--white)}
.card-photo{width:296px;height:192px}
.card h4{font-family:"Montserrat",Arial,sans-serif;font-weight:600;font-size:13px;color:#222;margin:24px 26px 6px}
.card p{font-size:12px;line-height:17px;margin:0 26px}
.card .more{display:block;margin:22px 26px 0;font-family:"Montserrat",Arial,sans-serif;font-weight:700;font-size:11px;color:var(--teal-dark)}

/* footer */
.footer{left:0;top:2438px;width:1200px;height:523px;background:var(--footer)}
.footer-curve{left:0;top:2420px;width:1200px;height:70px}
.footer-brand{left:112px;top:2595px;width:420px;text-align:center;font-family:"Montserrat",Arial,sans-serif;font-weight:700;font-size:24px;color:var(--white);white-space:nowrap}
.contact{left:132px;top:2726px;width:380px;text-align:center;color:var(--white);font-size:12px;line-height:18px}
.contact h5{font-family:"Montserrat",Arial,sans-serif;font-weight:700;font-size:12px;letter-spacing:.5px;margin-bottom:16px}
.map{left:559px;top:2525px;width:509px;height:288px;background:linear-gradient(135deg,#e8e6e1,#d9dfd6 60%,#e6e2d8)}
.footer-rule{left:132px;top:2866px;width:936px;height:1px;background:#555}
.follow{left:132px;top:2900px;display:flex;align-items:center;gap:8px;color:var(--white);font-family:"Montserrat",Arial,sans-serif;font-weight:700;font-size:11px}
.follow span.dot{width:24px;height:24px;border-radius:50%;background:#3d73c4;display:inline-block}
.follow .label{margin-right:12px}
.footer-nav{left:440px;top:2905px;font-size:11px;color:#ddd}
.copyright{right:132px;top:2905px;font-size:11px;color:#ddd}
</style>
</head>
<body>

<div class="abs hero" role="img" aria-label="Photo of a physiotherapist helping a smiling older man stretch a resistance band overhead"></div>
<svg class="abs hero-curve" viewBox="0 0 1200 100" preserveAspectRatio="none">
  <path d="M0 55 Q600 145 1200 55 L1200 100 L0 100 Z" fill="#ffffff"/>
  <path d="M0 55 Q600 145 1200 55" fill="none" stroke="#232a5c" stroke-width="5"/>
</svg>

<div class="abs brand"><span class="brand-dot"></span>Bayward Vale Physiotherapy</div>
<nav class="abs nav">
  <a class="active">Home</a><a>About Us</a><a>Services</a><a>Blog</a><a>Careers</a><a>Contact Us</a>
  <svg width="16" height="16" viewBox="0 0 16 16"><circle cx="6.5" cy="6.5" r="4.5" fill="none" stroke="#232a5c" stroke-width="2"/><path d="M10 10l4 4" stroke="#232a5c" stroke-width="2.4" stroke-linecap="round"/></svg>
</nav>
<h1 class="abs hero-title">PHYSIOTHERAPY</h1>
<span class="abs btn hero-btn">READ MORE</span>
<div class="abs dots"><span></span><span></span><span class="on"></span><span></span><span></span></div>

<h2 class="abs welcome-title">Welcome To Bayward Vale<br><b>Physiotherapy</b></h2>
<div class="abs welcome-copy">
  <p>Bayward Vale Physiotherapy is an innovative physiotherapy practice offering comprehensive services by experienced and highly-qualified physiotherapists.</p>
  <p>We achieve outstanding clinical results for a broad range of common conditions including: back pain, neck pain, headache, migraine, shoulder pain, sports injuries, vertigo, knee pain, incontinence, persistent pelvic pain and women's health and men's health issues.</p>
  <p>Our team of physiotherapists have extensive experience from working in private practice, private and public hospitals, and research and teaching over a range of physiotherapy disciplines including sports, manipulative, musculoskeletal, neurological, pain management, continence, women's / men's health and paediatric services.</p>
  <p>We are confident our practice will offer a service that stands apart, as we value excellence in quality care delivered by highly-educated and experienced physiotherapists.</p>
</div>
<span class="abs btn book-btn">BOOK ONLINE HERE*</span>
<p class="abs note">*Please note not all practitioners are available online – please call xx xxx xx to speak with our reception team.</p>
<div class="abs welcome-photo" role="img" aria-label="Photo of a physiotherapist treating a patient's leg on a treatment table"></div>

<svg class="abs services" viewBox="0 0 1200 700" preserveAspectRatio="none">
  <path d="M0 0 H1200 V665 Q600 610 0 665 Z" fill="#232a5c"/>
  <path d="M0 668 Q600 612 1200 668" fill="none" stroke="#78bea3" stroke-width="4"/>
</svg>
<h2 class="abs section-title services-title">OUR SERVICES</h2>
<div class="abs section-rule services-rule"></div>
<div class="abs grid-line" style="left:132px;top:1612px;width:936px;height:1px"></div>
<div class="abs grid-line" style="left:420px;top:1390px;width:1px;height:450px"></div>
<div class="abs grid-line" style="left:780px;top:1390px;width:1px;height:450px"></div>

<div class="abs service" style="left:91px;top:1390px">
  <svg width="56" height="56" viewBox="0 0 56 56"><circle cx="28" cy="28" r="22" fill="none" stroke="#78bea3" stroke-width="4"/><path d="M18 32l8-8 6 6 8-10" fill="none" stroke="#78bea3" stroke-width="4" stroke-linecap="round"/></svg>
  <h3>PHYSIOTHERAPY</h3>
  <p>Our team of experienced physiotherapists have a wide range of specialities and are well placed to diagnose and manage your problem.</p>
</div>
<div class="abs service" style="left:450px;top:1390px">
  <svg width="56" height="56" viewBox="0 0 56 56"><rect x="20" y="6" width="16" height="9" rx="3" fill="#78bea3"/><rect x="20" y="18" width="16" height="9" rx="3" fill="#78bea3"/><rect x="20" y="30" width="16" height="9" rx="3" fill="#78bea3"/><rect x="20" y="42" width="16" height="9" rx="3" fill="#78bea3"/></svg>
  <h3>CHRONIC PAIN MANAGEMENT</h3>
  <p>We all understand the complex nature of chronic pain and the need for a multidisciplinary, Biopsychosocial approach.</p>
</div>
<div class="abs service" style="left:811px;top:1390px">
  <svg width="56" height="56" viewBox="0 0 56 56"><circle cx="28" cy="28" r="10" fill="#78bea3"/><path d="M28 6v8M28 42v8M6 28h8M42 28h8" stroke="#78bea3" stroke-width="4" stroke-linecap="round"/></svg>
  <h3>KNEE CLINIC</h3>
  <p>The knee pain clinic provides a complete approach for those suffering from knee pain, recovering from knee surgery or knee injury.</p>
</div>
<div class="abs service" style="left:91px;top:1660px">
  <svg width="56" height="56" viewBox="0 0 56 56"><rect x="8" y="8" width="40" height="30" rx="3" fill="none" stroke="#78bea3" stroke-width="4"/><path d="M14 26q7-10 14 0t14 0" fill="none" stroke="#78bea3" stroke-width="3"/><rect x="22" y="42" width="12" height="8" fill="#78bea3"/></svg>
  <h3>REAL TIME ULTRASOUND</h3>
  <p>Physiotherapists use real-time ultrasound to examine how the small stabilising muscles of the spine are functioning.</p>
</div>
<div class="abs service" style="left:450px;top:1660px">
  <svg width="56" height="56" viewBox="0 0 56 56"><circle cx="17" cy="12" r="6" fill="#78bea3"/><rect x="11" y="21" width="12" height="30" rx="3" fill="#78bea3"/><circle cx="39" cy="12" r="6" fill="#78bea3"/><path d="M39 20l10 22H29z" fill="#78bea3"/><rect x="35" y="40" width="8" height="11" fill="#78bea3"/></svg>
  <h3>WOMEN'S &amp; MEN'S HEALTH</h3>
  <p>Our specialised Women's and Men's Health clinic is dedicated to addressing the often-distressing symptoms of incontinence, pelvic pain, and bladder and bowel dysfunction.</p>
</div>
<div class="abs service" style="left:811px;top:1660px">
  <svg width="56" height="56" viewBox="0 0 56 56"><path d="M28 50L8 30a11 11 0 0 1 20-14 11 11 0 0 1 20 14z" fill="#78bea3"/><path d="M28 22v16M20 30h16" stroke="#232a5c" stroke-width="5"/></svg>
  <h3>OTHER SERVICES</h3>
  <p>We have a range of other services available at Bayward Vale Physiotherapy. Click here for more information</p>
</div>

<div class="abs blog"></div>
<svg class="abs" style="left:0;top:1890px" width="1200" height="50" viewBox="0 0 1200 50" preserveAspectRatio="none">
  <path d="M0 13 Q600 -40 1200 13 L1200 0 L0 0 Z" fill="#232a5c"/>
  <path d="M0 15 Q600 -38 1200 15" fill="none" stroke="#78bea3" stroke-width="4"/>
</svg>
<h2 class="abs section-title blog-title">LATEST BLOG</h2>
<div class="abs section-rule blog-rule"></div>

<article class="abs card" style="left:132px">
  <div class="card-photo" role="img" aria-label="Photo of a woman exercising on a fitness ball" style="background:linear-gradient(135deg,#d9c3b3,#5c8fa3 60%,#b48a6e)"></div>
  <h4>There are many variations of pass</h4>
  <p>Lorem Ipsum is simply dummy text of the printing and typesetting industry</p>
  <span class="more">READ MORE ›</span>
</article>
<article class="abs card" style="left:454px">
  <div class="card-photo" role="img" aria-label="Photo of a physiotherapist assisting a patient with a leg stretch in a gym" style="background:linear-gradient(135deg,#c9423c,#d9a27a 50%,#5d6f9c)"></div>
  <h4>There are many variations of pass</h4>
  <p>Lorem Ipsum is simply dummy text of the printing and typesetting industry</p>
  <span class="more">READ MORE ›</span>
</article>
<article class="abs card" style="left:774px">
  <div class="card-photo" role="img" aria-label="Photo of a therapist supporting an older woman walking with a frame" style="background:linear-gradient(135deg,#e2c7a3,#6e8fa8 55%,#a36d4f)"></div>
  <h4>There are many variations of pass</h4>
  <p>Lorem Ipsum is simply dummy text of the printing and typesetting industry</p>
  <span class="more">READ MORE ›</span>
</article>

<div class="abs footer"></div>
<svg class="abs footer-curve" viewBox="0 0 1200 70" preserveAspectRatio="none">
  <path d="M0 18 Q600 -8 1200 18 L1200 0 L0 0 Z" fill="#f1f1f1"/>
  <path d="M0 18 Q600 -8 1200 18 L1200 26 Q600 2 0 26 Z" fill="#78bea3"/>
</svg>
<div class="abs footer-brand">Bayward Vale Physiotherapy</div>
<div class="abs contact">
  <h5>CONTACT US</h5>
  <p>52 Linden Road, Fairholm, VIC 3990</p>
  <p>hello@baywardvalephysiotherapy.com.au</p>
  <p>04 XXXX XXXX</p>
</div>
<div class="abs map" role="img" aria-label="Street map showing the clinic location"></div>
<div class="abs footer-rule"></div>
<div class="abs follow"><span class="label">FOLLOW US</span><span class="dot"></span><span class="dot" style="background:#3aa0e0"></span><span class="dot" style="background:#2a5fa8"></span></div>
<div class="abs footer-nav">Home &nbsp;|&nbsp; About us &nbsp;|&nbsp; Services &nbsp;|&nbsp; Blog &nbsp;|&nbsp; Careers &nbsp;|&nbsp; Contact Us</div>
<div class="abs copyright">Copyrights @ 2018 All Rights Reserved</div>

</body>
</html>
```